Modern Verdell Tree Care Website

I need a website for a full service Tree Care company. The company provides tree pruning, tree removal, tree preservation, emergency services, stump grinding, and emergency tree services.

Target Market(s)

Customers that need tree services

Industry/Entity Type

Landscaping, Tree Services

Coding

Coded - Design and coding required

Number of Pages Required

5+ page

Font styles to use
Sans Serif

Requirements
Must have
• Good clean design that showcases the services the company provides.
Nice to have
• Services page; contact form, blog, home page, about page

```html
<!DOCTYPE html>
<html lang="en">
<head>
<meta charset="utf-8">
<title>Verdell Tree Care</title>
<link href="https://fonts.googleapis.com/css2?family=Lexend:wght@300;400;500;600&family=Syncopate:wght@700&display=swap" rel="stylesheet">
<style>
:root{
  --green:#8dc63f;
  --green-dark:#6f9e2a;
  --orange:#e38b1f;
  --ink:#1b1c1b;
  --panel:#262726;
  --panel-hover:#4b5b5a;
  --text-light:#d9dcd6;
  --text-muted:#a9aca6;
  --white:#ffffff;
  --slate:#4b5b5a;
}
*{box-sizing:border-box;margin:0;padding:0}
html,body{width:1200px;height:4800px;overflow:hidden}
body{position:relative;font-family:'Lexend',sans-serif;background:var(--white);color:var(--ink)}
h1,h2,h3,h4{font-weight:400}
.abs{position:absolute}
.display{font-family:'Syncopate',sans-serif;font-weight:700;text-transform:uppercase;letter-spacing:1px}
.accent{color:var(--green)}
.btn-outline{position:absolute;display:flex;align-items:center;justify-content:center;gap:10px;border:1.5px solid var(--green);color:var(--white);font-size:13px;height:42px;width:140px}
.btn-outline svg{width:14px;height:10px}

.site-header{left:0;top:0;width:1200px;height:63px;background:var(--ink);z-index:5}
.brand{left:67px;top:12px;display:flex;align-items:center;gap:10px}
.brand-mark{width:30px;height:30px;background:var(--green)}
.brand-name{font-size:18px;font-weight:600;color:var(--white);letter-spacing:2px;line-height:1}
.main-nav a{position:absolute;top:24px;font-size:13px;color:var(--white);text-decoration:none}
.main-nav a.active{color:var(--green)}
.main-nav a.active::after{content:"";position:absolute;left:0;right:0;bottom:-6px;height:2px;background:var(--green)}
.header-phone{left:1018px;top:23px;font-size:13px;color:var(--white);display:flex;gap:8px;align-items:center}

.hero{left:0;top:63px;width:1200px;height:701px;background:linear-gradient(90deg,#2a2f27 0%,#2f3529 35%,#3e4a33 100%)}
.hero-photo{left:410px;top:63px;width:790px;height:701px;background:linear-gradient(135deg,#6a5a45 0%,#4b5a3a 45%,#2c3426 100%)}
.hero-eyebrow{left:67px;top:245px;font-size:19px;color:var(--green);letter-spacing:3px}
.hero-title{left:67px;top:276px;font-size:37px;line-height:56px;color:var(--white)}
.hero-text{left:67px;top:400px;width:400px;font-size:14px;line-height:24px;color:var(--text-light)}
.hero-dots{left:67px;top:604px;display:flex;gap:14px}
.hero-dots span{width:5px;height:5px;border-radius:50%;background:var(--orange)}

.stats{left:67px;top:680px;width:1066px;height:168px;background:var(--white);display:flex;z-index:3}
.stat{flex:1;display:flex;flex-direction:column;align-items:center;justify-content:center;position:relative}
.stat+.stat::before{content:"";position:absolute;left:0;top:32px;bottom:32px;width:1px;background:#dcdcdc}
.stat-value{font-size:38px;color:var(--green-dark);font-weight:400}
.stat-label{font-size:16px;letter-spacing:2px;margin-top:8px;color:#333}

.about{left:0;top:764px;width:1200px;height:650px;background:linear-gradient(180deg,#2c2d29 0%,#3a3b31 50%,#2f3128 100%)}
.about-photo{left:67px;top:909px;width:455px;height:455px;border-radius:40px 220px 0 40px;background:linear-gradient(160deg,#7b8a4c 0%,#5c5c38 50%,#8a6a48 100%)}
.about-title{left:559px;top:990px;font-size:28px;color:var(--white)}
.about-text{left:559px;top:1046px;width:575px;font-size:13.5px;line-height:25px;color:var(--text-light)}
.about-text p+p{margin-top:12px}

.section-title{left:0;width:1200px;text-align:center;font-size:28px;color:var(--ink)}
.card{position:absolute;width:345px;background:var(--panel);border-radius:14px}
.card.is-hover{background:var(--panel-hover)}
.card-photo{position:absolute;left:15px;top:15px;width:315px;height:216px;border-radius:8px}
.card-title{position:absolute;left:15px;top:250px;font-size:19px;font-weight:400;color:var(--white)}
.card-text{position:absolute;left:15px;top:290px;width:315px;font-size:12.5px;line-height:22px;color:var(--text-muted)}
.card .btn-outline{left:15px;top:376px}
.view-all{left:512px;top:2515px;width:177px;height:45px;background:var(--slate);color:var(--white);font-size:13px;display:flex;align-items:center;justify-content:center;letter-spacing:.5px}

.contact{left:0;top:2662px;width:1200px;height:473px;background:linear-gradient(90deg,#1f241d 0%,#2e3627 100%)}
.contact-photo{left:620px;top:2662px;width:580px;height:473px;background:linear-gradient(120deg,#b9793a 0%,#7c5a3c 40%,#546a3a 100%)}
.contact-eyebrow{left:67px;top:2752px;font-size:17px;color:var(--orange)}
.contact-title{left:67px;top:2788px;font-size:28px;line-height:46px;color:var(--white)}
.field{position:absolute;background:var(--white);font-size:12px;color:#888;padding:10px 10px;border:1px solid #ccc}
.submit{position:absolute;left:67px;top:3003px;width:237px;height:41px;border:1.5px solid var(--green);color:var(--white);font-size:13px;display:flex;align-items:center;justify-content:center}

.blog-card{position:absolute;width:345px;height:417px;top:3294px;background:var(--panel);border-radius:14px}
.blog-photo{position:absolute;left:15px;top:15px;width:315px;height:201px;border-radius:8px}
.blog-date{position:absolute;left:28px;top:208px;display:flex;align-items:center;gap:10px}
.blog-date b{width:32px;height:32px;background:var(--orange);color:var(--white);font-size:15px;font-weight:500;display:flex;align-items:center;justify-content:center;border-radius:3px}
.blog-date span{font-size:11px;color:var(--white);margin-top:14px}
.blog-title{position:absolute;left:15px;top:268px;width:320px;font-size:19px;line-height:28px;font-weight:500;color:var(--white)}
.blog-card .btn-outline{left:15px;top:344px}

.why{left:0;top:3813px;width:1200px;height:539px;background:linear-gradient(90deg,#1f221d 0%,#2b3126 100%)}
.why-title{left:67px;top:3878px;font-size:28px;color:var(--white)}
.why-text{left:67px;top:3944px;width:460px;font-size:14px;line-height:27px;color:var(--text-muted)}
.why-list{left:67px;top:4026px;list-style:none}
.why-list li{display:flex;align-items:center;gap:10px;height:38px;font-size:13px;color:var(--white)}
.why-list svg{width:24px;height:24px}
.why-main{left:727px;top:3884px;width:395px;height:397px;border-radius:16px;background:linear-gradient(160deg,#4c6a8a 0%,#6a6a4a 45%,#a07a4a 100%)}
.why-small{border:6px solid var(--white);border-radius:14px}
.why-small.top{left:587px;top:3877px;width:134px;height:130px;background:linear-gradient(135deg,#c9a98a,#8a6a55)}
.why-small.bottom{left:1022px;top:4190px;width:106px;height:100px;background:linear-gradient(135deg,#6c8a5a,#3e4e32)}

.site-footer{left:0;top:4352px;width:1200px;height:448px;background:var(--ink)}
.footer-heading{font-size:19px;font-weight:500;color:var(--green)}
.footer-links{list-style:none}
.footer-links li{font-size:13px;color:var(--text-light);height:34px}
.footer-brand{left:480px;top:4428px;display:flex;align-items:center;gap:14px}
.footer-brand .brand-mark{width:56px;height:56px}
.footer-brand .brand-name{font-size:32px;letter-spacing:4px}
.footer-nav{left:0;width:1200px;top:4524px;text-align:center;font-size:11.5px;color:var(--text-light);letter-spacing:.5px}
.follow{left:0;width:1200px;top:4580px;text-align:center;font-size:14px;color:var(--white)}
.socials{left:490px;top:4618px;display:flex;gap:12px}
.socials span{width:34px;height:34px;background:var(--white);border-radius:3px}
.socials span.on{background:#7f8c9a}
.contact-item{position:absolute;left:881px;display:flex;gap:16px;font-size:13px;line-height:21px;color:var(--text-light)}
.contact-item svg{width:16px;height:16px;flex:none;margin-top:2px}
.footer-rule{left:67px;top:4728px;width:1066px;height:1px;background:#333}
.legal{left:67px;top:4746px;font-size:10px;color:var(--text-light)}
.copyright{left:0;width:1200px;top:4744px;text-align:center;font-size:12px;color:var(--text-light)}
</style>
</head>
<body>

<header class="abs site-header">
  <div class="abs brand">
    <span class="brand-mark"></span>
    <span class="brand-name">VERDELL</span>
  </div>
  <nav class="main-nav">
    <a class="active" style="left:436px">HOME</a>
    <a style="left:535px">ABOUT US</a>
    <a style="left:663px">SERVICES</a>
    <a style="left:787px">BLOG</a>
    <a style="left:880px">CONTACT US</a>
  </nav>
  <div class="abs header-phone">
    <svg width="14" height="14" viewBox="0 0 24 24"><path d="M6.6 10.8a15 15 0 006.6 6.6l2.2-2.2c.3-.3.7-.4 1-.2 1.1.4 2.3.6 3.6.6.6 0 1 .4 1 1V20c0 .6-.4 1-1 1A17 17 0 013 4c0-.6.4-1 1-1h3.5c.6 0 1 .4 1 1 0 1.3.2 2.5.6 3.6.1.3 0 .7-.2 1z" fill="#e38b1f"/></svg>
    (555) 214-0387
  </div>
</header>

<section>
  <div class="abs hero"></div>
  <div class="abs hero-photo" role="img" aria-label="Arborist in safety gear cutting a tree trunk with a chainsaw"></div>
  <div class="abs hero-eyebrow">VERDELL FOR</div>
  <h1 class="abs display hero-title">All your <span class="accent">tree</span><br>care needs</h1>
  <p class="abs hero-text">Duis aute irure dolor in reprehenderit in voluptate velit esse cillum dolore eu fugiat</p>
  <a class="btn-outline" style="left:67px;top:477px;width:177px;height:47px">Request A Quote <svg viewBox="0 0 14 10"><path d="M0 5h12M8 1l4 4-4 4" stroke="#fff" fill="none" stroke-width="1.4"/></svg></a>
  <div class="abs hero-dots"><span></span><span></span><span></span></div>
</section>

<div class="abs stats">
  <div class="stat"><span class="stat-value">7/10</span><span class="stat-label">TOP US</span></div>
  <div class="stat"><span class="stat-value">100</span><span class="stat-label">CLIENT REVIEW</span></div>
  <div class="stat"><span class="stat-value">2/3</span><span class="stat-label">BEST PRICE</span></div>
  <div class="stat"><span class="stat-value">300</span><span class="stat-label">ORIGINAL EQUIPMENT</span></div>
</div>

<section>
  <div class="abs about"></div>
  <div class="abs about-photo" role="img" aria-label="Worker cutting a log with a chainsaw in the forest"></div>
  <h2 class="abs display about-title">Who we <span class="accent">are</span></h2>
  <div class="abs about-text">
    <p>At Verdell Tree Care, we are more than just a tree service company, we are stewards of our beautiful trees. With a passion deeply rooted in arboriculture, we embark on a mission to promote the health, beauty, and safety of your trees and landscapes.</p>
    <p>Whether it's expert tree trimming to enhance aesthetics, meticulous tree removal to mitigate hazards, or comprehensive tree health assessments to ensure safety, we approach each task with unwavering dedication and attention to detail.</p>
  </div>
  <a class="btn-outline" style="left:559px;top:1235px;width:137px;height:43px">Read More <svg viewBox="0 0 14 10"><path d="M0 5h12M8 1l4 4-4 4" stroke="#fff" fill="none" stroke-width="1.4"/></svg></a>
</section>

<section>
  <h2 class="abs display section-title" style="top:1510px">Our <span class="accent">services</span></h2>

  <article class="card is-hover" style="left:67px;top:1574px;height:440px">
    <div class="card-photo" role="img" aria-label="Man trimming hedge branches with loppers" style="background:linear-gradient(135deg,#3f6a2a,#7a3a2a)"></div>
    <h3 class="card-title"><span class="accent">Tree</span> Trimming</h3>
    <p class="card-text">Sed ut perspiciatis unde omnis iste natus error sit voluptatem accusantium doloremque laudantium</p>
    <a class="btn-outline">Read More <svg viewBox="0 0 14 10"><path d="M0 5h12M8 1l4 4-4 4" stroke="#fff" fill="none" stroke-width="1.4"/></svg></a>
  </article>
  <article class="card" style="left:428px;top:1574px;height:440px">
    <div class="card-photo" role="img" aria-label="Climber cutting a tree trunk with a chainsaw" style="background:linear-gradient(135deg,#9aa6b0,#4a3f35)"></div>
    <h3 class="card-title"><span class="accent">Tree</span> Removal</h3>
    <p class="card-text">Sed ut perspiciatis unde omnis iste natus error sit voluptatem accusantium doloremque laudantium</p>
    <a class="btn-outline">Read More <svg viewBox="0 0 14 10"><path d="M0 5h12M8 1l4 4-4 4" stroke="#fff" fill="none" stroke-width="1.4"/></svg></a>
  </article>
  <article class="card" style="left:788px;top:1574px;height:440px">
    <div class="card-photo" role="img" aria-label="Workers clearing land and planting saplings" style="background:linear-gradient(180deg,#b9c6c9,#6d7a4a)"></div>
    <h3 class="card-title"><span class="accent">Tree</span> Clearing</h3>
    <p class="card-text">Sed ut perspiciatis unde omnis iste natus error sit voluptatem accusantium doloremque laudantium</p>
    <a class="btn-outline">Read More <svg viewBox="0 0 14 10"><path d="M0 5h12M8 1l4 4-4 4" stroke="#fff" fill="none" stroke-width="1.4"/></svg></a>
  </article>

  <article class="card" style="left:67px;top:2031px;height:441px">
    <div class="card-photo" role="img" aria-label="Gardener pruning a tree with a saw" style="background:linear-gradient(135deg,#9ab08a,#5a7a3a)"></div>
    <h3 class="card-title"><span class="accent">Tree</span> Pruning</h3>
    <p class="card-text">Sed ut perspiciatis unde omnis iste natus error sit voluptatem accusantium doloremque laudantium</p>
    <a class="btn-outline">Read More <svg viewBox="0 0 14 10"><path d="M0 5h12M8 1l4 4-4 4" stroke="#fff" fill="none" stroke-width="1.4"/></svg></a>
  </article>
  <article class="card" style="left:428px;top:2031px;height:441px">
    <div class="card-photo" role="img" aria-label="Operator at a sawmill cutting a large log" style="background:linear-gradient(135deg,#d06a2a,#8a6a4a)"></div>
    <h3 class="card-title"><span class="accent">Stump</span> Grinding</h3>
    <p class="card-text">Sed ut perspiciatis unde omnis iste natus error sit voluptatem accusantium doloremque laudantium</p>
    <a class="btn-outline">Read More <svg viewBox="0 0 14 10"><path d="M0 5h12M8 1l4 4-4 4" stroke="#fff" fill="none" stroke-width="1.4"/></svg></a>
  </article>
  <article class="card" style="left:788px;top:2031px;height:441px">
    <div class="card-photo" role="img" aria-label="Volunteers planting and watering a young tree" style="background:linear-gradient(135deg,#8aa070,#4a5a35)"></div>
    <h3 class="card-title"><span class="accent">Tree</span> Preservation</h3>
    <p class="card-text">Sed ut perspiciatis unde omnis iste natus error sit voluptatem accusantium doloremque laudantium</p>
    <a class="btn-outline">Read More <svg viewBox="0 0 14 10"><path d="M0 5h12M8 1l4 4-4 4" stroke="#fff" fill="none" stroke-width="1.4"/></svg></a>
  </article>

  <a class="abs view-all">VIEW ALL SERVICES</a>
</section>

<section>
  <div class="abs contact"></div>
  <div class="abs contact-photo" role="img" aria-label="Lumberjack in helmet sawing through a thick log"></div>
  <div class="abs contact-eyebrow">CONTACT US</div>
  <h2 class="abs display contact-title">If you have any<br><span class="accent">question</span></h2>
  <div class="field" style="left:67px;top:2902px;width:237px;height:42px">Name:</div>
  <div class="field" style="left:311px;top:2902px;width:239px;height:42px">Email:</div>
  <div class="field" style="left:67px;top:2953px;width:237px;height:41px">Phone:</div>
  <div class="field" style="left:311px;top:2953px;width:239px;height:91px">Message:</div>
  <div class="submit">Submit</div>
</section>

<section>
  <h2 class="abs display section-title" style="top:3231px">Recent <span class="accent">blog</span></h2>

  <article class="blog-card" style="left:67px">
    <div class="blog-photo" role="img" aria-label="Two foresters measuring a tree trunk" style="background:linear-gradient(135deg,#7a6a4a,#4a5a3a)"></div>
    <div class="blog-date"><b>23</b><span>MAY, 2024</span></div>
    <h3 class="blog-title">Reprehenderit qui in ea voluptate velit esse quam nihil</h3>
    <a class="btn-outline">Read More <svg viewBox="0 0 14 10"><path d="M0 5h12M8 1l4 4-4 4" stroke="#fff" fill="none" stroke-width="1.4"/></svg></a>
  </article>
  <article class="blog-card" style="left:428px">
    <div class="blog-photo" role="img" aria-label="Chainsaw cutting a fallen log on the forest floor" style="background:linear-gradient(135deg,#5a4a3a,#a08a6a)"></div>
    <div class="blog-date"><b>15</b><span>MAY, 2024</span></div>
    <h3 class="blog-title">Reprehenderit qui in ea voluptate velit esse quam nihil</h3>
    <a class="btn-outline">Read More <svg viewBox="0 0 14 10"><path d="M0 5h12M8 1l4 4-4 4" stroke="#fff" fill="none" stroke-width="1.4"/></svg></a>
  </article>
  <article class="blog-card" style="left:788px">
    <div class="blog-photo" role="img" aria-label="Forester standing among tall pine trunks" style="background:linear-gradient(135deg,#6a6a5a,#3a3a2a)"></div>
    <div class="blog-date"><b>12</b><span>APRIL, 2024</span></div>
    <h3 class="blog-title">Reprehenderit qui in ea voluptate velit esse quam nihil</h3>
    <a class="btn-outline">Read More <svg viewBox="0 0 14 10"><path d="M0 5h12M8 1l4 4-4 4" stroke="#fff" fill="none" stroke-width="1.4"/></svg></a>
  </article>
</section>

<section>
  <div class="abs why"></div>
  <h2 class="abs display why-title">Why choose <span class="accent">us</span></h2>
  <p class="abs why-text">Sed ut perspiciatis unde omnis iste natus error sit voluptatem accusantium doloremque laudantium</p>
  <ul class="abs why-list">
    <li><svg viewBox="0 0 24 24"><circle cx="12" cy="12" r="10" fill="none" stroke="#8dc63f" stroke-width="1.6"/><path d="M7 12.5l3.2 3L17 9" fill="none" stroke="#8dc63f" stroke-width="1.8"/></svg>Licensed and Insured</li>
    <li><svg viewBox="0 0 24 24"><circle cx="12" cy="12" r="10" fill="none" stroke="#8dc63f" stroke-width="1.6"/><path d="M7 12.5l3.2 3L17 9" fill="none" stroke="#8dc63f" stroke-width="1.8"/></svg>24 Hours Emergency Services</li>
    <li><svg viewBox="0 0 24 24"><circle cx="12" cy="12" r="10" fill="none" stroke="#8dc63f" stroke-width="1.6"/><path d="M7 12.5l3.2 3L17 9" fill="none" stroke="#8dc63f" stroke-width="1.8"/></svg>Locally Owned &amp; Operated</li>
    <li><svg viewBox="0 0 24 24"><circle cx="12" cy="12" r="10" fill="none" stroke="#8dc63f" stroke-width="1.6"/><path d="M7 12.5l3.2 3L17 9" fill="none" stroke="#8dc63f" stroke-width="1.8"/></svg>Professionl Work</li>
    <li><svg viewBox="0 0 24 24"><circle cx="12" cy="12" r="10" fill="none" stroke="#8dc63f" stroke-width="1.6"/><path d="M7 12.5l3.2 3L17 9" fill="none" stroke="#8dc63f" stroke-width="1.8"/></svg>Safety is Our No 1 priority</li>
    <li><svg viewBox="0 0 24 24"><circle cx="12" cy="12" r="10" fill="none" stroke="#8dc63f" stroke-width="1.6"/><path d="M7 12.5l3.2 3L17 9" fill="none" stroke="#8dc63f" stroke-width="1.8"/></svg>Free Estimate</li>
    <li><svg viewBox="0 0 24 24"><circle cx="12" cy="12" r="10" fill="none" stroke="#8dc63f" stroke-width="1.6"/><path d="M7 12.5l3.2 3L17 9" fill="none" stroke="#8dc63f" stroke-width="1.8"/></svg>Licensed Arborist on Staff</li>
  </ul>
  <div class="abs why-main" role="img" aria-label="Chainsaw resting on freshly cut logs in a forest"></div>
  <div class="abs why-small top" role="img" aria-label="Stack of cut firewood"></div>
  <div class="abs why-small bottom" role="img" aria-label="Worker stacking wood in a yard"></div>
</section>

<footer class="abs site-footer"></footer>
<div class="abs" style="left:67px;top:4425px">
  <h4 class="footer-heading">SERVICES</h4>
  <ul class="footer-links" style="margin-top:24px">
    <li>Tree Pruning</li><li>Tree Removal</li><li>Tree Preservation</li><li>Emergency Services</li><li>Stump Grinding</li><li>Emergency Tree Services</li>
  </ul>
</div>
<div class="abs footer-brand">
  <span class="brand-mark"></span>
  <span class="brand-name">VERDELL</span>
</div>
<div class="abs footer-nav">HOME &nbsp;|&nbsp; ABOUT US &nbsp;|&nbsp; SERVICES &nbsp;|&nbsp; BLOG &nbsp;|&nbsp; CONTACT US</div>
<div class="abs follow">FOLLOW US</div>
<div class="abs socials" aria-label="Social media links"><span></span><span class="on"></span><span></span><span></span><span></span></div>
<h4 class="abs footer-heading" style="left:881px;top:4425px">CONTACTS</h4>
<div class="contact-item" style="top:4480px">
  <svg viewBox="0 0 24 24"><path d="M12 2a7 7 0 00-7 7c0 5 7 13 7 13s7-8 7-13a7 7 0 00-7-7zm0 9.5A2.5 2.5 0 1112 6.5a2.5 2.5 0 010 5z" fill="#e38b1f"/></svg>
  <span>87 Lorem ipsum dolar sit amet<br>Brookfield 40RT USA</span>
</div>
<div class="contact-item" style="top:4548px">
  <svg viewBox="0 0 24 24"><path d="M6.6 10.8a15 15 0 006.6 6.6l2.2-2.2c.3-.3.7-.4 1-.2 1.1.4 2.3.6 3.6.6.6 0 1 .4 1 1V20c0 .6-.4 1-1 1A17 17 0 013 4c0-.6.4-1 1-1h3.5c.6 0 1 .4 1 1 0 1.3.2 2.5.6 3.6.1.3 0 .7-.2 1z" fill="#e38b1f"/></svg>
  <span>(555) 214-0387 / (555) 309-4412</span>
</div>
<div class="contact-item" style="top:4606px">
  <svg viewBox="0 0 24 24"><rect x="2" y="5" width="20" height="14" rx="1" fill="#e38b1f"/><path d="M2 6l10 7 10-7" fill="none" stroke="#1b1c1b" stroke-width="1.5"/></svg>
  <span>info@verdelltreecare.com</span>
</div>
<div class="abs footer-rule"></div>
<div class="abs legal">Terms &amp; Condition &nbsp;|&nbsp; Privacy Policy</div>
<div class="abs copyright">© <span class="accent">Verdell Tree Care</span>, 2024. All Rights Reserved.</div>

</body>
</html>
```